real esate business card with company logo and name

we need a business card design for a real esate company

The company name is Walsh & Brand Pty Ltd, and we have our logo designed and will upload. We want classic or moden feel. Black or white background. looks more textured. Should include folowinginformations
Owen Walsh and Lucy Brand
Sales Agents & Onsite Manager
p: 07 5948 2063
F: 07 5948 2174
M:0431 857 219
3/42 Marlow Crescent, FERNLEA QLD 4213

We want this business card looks professonal. Thank you in advance.

Industry/Entity Type

Real Estate Agent

Contact Information for Business Card

Owen Walsh and Lucy Brand
Onsite Manager & Sales Agents
p: 07 5948 2063
M:0431 857 219

Font styles to use
Serif

Colors
000000
fbfbfb
333333
959595

Requirements
Must have
• company logo and name, black or white back ground

```html
<!DOCTYPE html>
<html lang="en">
<head>
<meta charset="utf-8">
<title>Walsh &amp; Brand Pty Ltd – Business Card</title>
<link rel="stylesheet" href="https://fonts.googleapis.com/css2?family=Tinos:wght@400;700&display=swap">
<style>
  :root {
    --ink: #000000;
    --paper: #fbfbfb;
    --charcoal: #333333;
    --silver: #959595;
    --stage: #e4e2df;
    --swoosh: #8f9194;
    --swoosh-light: #c9cacc;
  }
  html, body {
    margin: 0;
    width: 1200px;
    height: 892px;
    overflow: hidden;
    background: var(--stage);
  }
  .card {
    position: absolute;
    left: 100px;
    top: 160px;
    width: 1000px;
    height: 571px;
    background: var(--paper);
    box-shadow: 0 6px 22px rgba(0,0,0,0.18);
    overflow: hidden;
    font-family: "Tinos", "Times New Roman", serif;
  }
  .card-art {
    position: absolute;
    inset: 0;
    width: 1000px;
    height: 571px;
  }
  .brand {
    position: absolute;
    left: 470px;
    top: 52px;
    display: flex;
    align-items: center;
    gap: 16px;
  }
  .brand-mark {
    width: 58px;
    height: 58px;
    background: var(--silver);
  }
  .brand-name {
    font-size: 24px;
    letter-spacing: 2px;
    color: var(--silver);
    text-transform: uppercase;
  }
  .details {
    position: absolute;
    left: 470px;
    top: 190px;
    color: var(--ink);
  }
  .agents {
    margin: 0;
    font-size: 42px;
    line-height: 1.1;
  }
  .role {
    margin: 6px 0 30px;
    font-size: 31px;
    color: var(--silver);
  }
  .contact {
    margin: 0;
    font-size: 31px;
    line-height: 1.32;
  }
</style>
</head>
<body>
  <article class="card">
    <svg class="card-art" viewBox="0 0 1000 571" aria-hidden="false">
      <defs>
        <linearGradient id="photoTone" x1="0" y1="0" x2="0" y2="1">
          <stop offset="0" stop-color="#b9cfe0"/>
          <stop offset="0.3" stop-color="#dde4e6"/>
          <stop offset="0.5" stop-color="#d7653a"/>
          <stop offset="0.72" stop-color="#ece9e3"/>
          <stop offset="1" stop-color="#5f9a3c"/>
        </linearGradient>
      </defs>
      <path class="swoosh-band" d="M0 0 H338 C380 200 395 400 500 571 H0 Z" fill="var(--swoosh-light)"/>
      <path class="swoosh-edge" d="M0 0 H322 C362 200 378 400 478 571 H0 Z" fill="var(--swoosh)"/>
      <path class="house-photo" role="img" aria-label="Photo of a two-storey white house with an orange tiled roof and green lawn"
            d="M0 0 H300 C340 200 356 400 452 571 H0 Z" fill="url(#photoTone)"/>
    </svg>

    <div class="brand">
      <span class="brand-mark"></span>
      <span class="brand-name">Walsh &amp; Brand Pty Ltd.</span>
    </div>

    <div class="details">
      <h1 class="agents">Owen Walsh and Lucy Brand</h1>
      <p class="role">Onsite Manager &amp; Sales Agents</p>
      <p class="contact">07 5948 2063<br>0431 857 219<br>3/42 Marlow Crescent, FERNLEA<br>QLD 4213</p>
    </div>
  </article>
</body>
</html>
```